Existing Website Requiring new Pages

I have an existing word press website that was built using elementor.
Website: www.tallowcrestcare.com.au
I require the Vacancies page (https://www.tallowcrestcare.com.au/vacancies/) to be modified to display our new properties along with minor tweaks to how the information is presented.
The vacancies to be displayed are the exactly the same as those that are located on the homepage of QMR website (https://qmr.org.au/)
The new pages that link off the Vacancies tab will require custom design.
There are roughly 8 pages/properties to be incorporated. i wish for the design to be very similar to that displayed in the following link; https://www.polunda.com.au/vacancies/merrylands
Along with this the back end has not been updated for the last 3 years so it also requires some maintenance.
Website is in the disability industry and the custom pages will display information relative to Property Vacancies.
I have attached a ZIP file with some design guides, the information for each of the properties (which will need to be modified to show our business name Tallowcrest Care) and the example of how it is to look based off the Polunda website.
If you guys have any suggestions or ideas on how to make this more presentable or possible i'm open to your ideas.
Target Market(s)
People looking for SDA properties custom built for people with a disability
Industry/Entity Type
Disability
Coding
Coded - Design and coding required
Number of Pages Required
5+ page

```html
<!DOCTYPE html>
<html lang="en">
<head>
<meta charset="utf-8">
<title>Vacancies – Tallowcrest Care</title>
<link href="https://fonts.googleapis.com/css2?family=Montserrat:wght@400;500;600;700&display=swap" rel="stylesheet">
<style>
:root{
  --ink:#1c1c1c;
  --nav:#2b2b2b;
  --accent:#f08a4b;
  --brand:#d9468c;
  --teal:#19c5c9;
  --muted:#8a8a8a;
  --footer-bg:#f6f6f7;
  --bar:#1e1e1e;
  --rule:#e2e2e2;
  --blue:#1e88e5;
}
*{box-sizing:border-box;margin:0;padding:0}
html,body{width:874px;height:1200px;overflow:hidden;background:#fff}
body{position:relative;font-family:'Montserrat',sans-serif;color:var(--ink)}
.abs{position:absolute}

/* header */
.site-header{position:absolute;left:0;top:0;width:874px;height:97px;background:#fff}
.brand{position:absolute;left:72px;top:30px;display:flex;align-items:center;gap:6px}
.brand-dot{width:12px;height:12px;border-radius:50%;background:var(--teal)}
.brand-name{font-size:13px;font-weight:600;color:var(--brand);letter-spacing:.5px}
.main-nav{position:absolute;top:40px;left:410px;display:flex;gap:17px;font-size:7.8px;font-weight:700;letter-spacing:.4px;color:var(--nav)}
.main-nav .current{color:var(--accent)}

/* hero */
.hero{position:absolute;left:0;top:97px;width:874px;height:375px;
  background:linear-gradient(100deg,#3a2a44 0%,#2c2436 35%,#3b3a3a 65%,#4d4a3a 100%)}
.hero-tree{position:absolute;left:18px;top:70px;width:310px;height:200px;border-radius:50% 50% 40% 40%;
  background:radial-gradient(ellipse at 45% 50%,rgba(226,60,160,.75),rgba(226,60,160,0) 70%)}
.hero-people{position:absolute;left:620px;top:50px;width:240px;height:300px;
  background:radial-gradient(ellipse at 50% 55%,rgba(190,140,110,.55),rgba(190,140,110,0) 70%)}
.hero-title{position:absolute;left:448px;top:160px;font-size:28px;font-weight:600;color:#fff;letter-spacing:.3px}
.hero-grass{position:absolute;left:0;bottom:0;width:874px;height:22px;
  background:linear-gradient(90deg,var(--teal) 0%,var(--teal) 22%,#f5a25a 30%,#f5a25a 68%,var(--teal) 74%,var(--teal) 100%)}

/* property grid */
.property{position:absolute;width:177px;height:174px}
.property-photo{position:absolute;left:0;top:0;width:177px;height:122px;border-radius:4px}
.property-card{position:absolute;left:11px;top:98px;width:156px;height:74px;background:#fff;border-radius:4px;
  box-shadow:0 2px 6px rgba(0,0,0,.14);text-align:center}
.property-name{margin-top:14px;font-size:14.5px;font-weight:500;color:var(--ink)}
.property-type{margin-top:7px;font-size:11px;font-weight:400;color:var(--ink)}
.sky-a{background:linear-gradient(180deg,#dfe7ef 0%,#c9d4dc 45%,#6f8a5a 75%,#8a8a86 100%)}
.sky-b{background:linear-gradient(180deg,#a9c8e6 0%,#b47a5c 45%,#7aa351 80%,#b38f7a 100%)}
.sky-c{background:linear-gradient(180deg,#7fb3e0 0%,#cdb68c 50%,#4f7a3c 80%,#c9b79a 100%)}
.sky-d{background:linear-gradient(180deg,#8db8e0 0%,#e7d8c2 45%,#c9b59c 80%,#7f9e5e 100%)}
.sky-e{background:linear-gradient(180deg,#5ea4e4 0%,#cdb39a 55%,#6aa14a 85%)}
.sky-f{background:linear-gradient(180deg,#8bb9e5 0%,#c76a45 50%,#6ea84b 75%,#bcb7b0 100%)}
.sky-g{background:linear-gradient(180deg,#e2b36a 0%,#8a6a4c 45%,#4f6a3c 85%)}
.sky-h{background:linear-gradient(180deg,#eef0ea 0%,#c9d3c0 40%,#a07a72 75%,#7a6a60 100%)}

/* footer */
.site-footer{position:absolute;left:0;top:937px;width:874px;height:219px;background:var(--footer-bg)}
.footer-brand{position:absolute;left:76px;top:55px;display:flex;align-items:center;gap:6px}
.contact-list{position:absolute;left:72px;top:146px;list-style:none;font-size:9px;color:var(--muted)}
.contact-list li{display:flex;align-items:center;gap:7px;height:16.5px}
.contact-list svg{width:11px;height:11px}
.badges{position:absolute;left:379px;top:41px;display:flex;flex-direction:column;gap:6px}
.badge{width:24px;height:24px;border-radius:50%}
.footer-col{position:absolute;top:31px;width:170px}
.footer-col h3{font-size:10.5px;font-weight:500;color:var(--ink);border-left:2px solid var(--blue);padding-left:9px;letter-spacing:.3px;height:12px;line-height:12px}
.footer-col ul{list-style:none;margin-top:12px}
.footer-col li{font-size:9px;color:var(--muted);border-top:1px solid var(--rule);padding:7px 0 7px;line-height:1.45}
.footer-col li:last-child{border-bottom:1px solid var(--rule)}
.bottom-bar{position:absolute;left:0;top:1156px;width:874px;height:44px;background:var(--bar);
  color:#fff;font-size:9px;font-weight:600;text-align:center;line-height:44px}
</style>
</head>
<body>

<header class="site-header">
  <div class="brand"><span class="brand-dot"></span><span class="brand-name">TALLOWCREST CARE</span></div>
  <nav class="main-nav">
    <span>HOME</span><span>ABOUT US</span><span class="current">WHAT WE DO ⌄</span><span>REFERRALS</span><span>FEEDBACK</span><span>CONTACT US</span>
  </nav>
</header>

<section class="hero" role="img" aria-label="Evening park scene with a colourful tree illustration, carer and wheelchair user silhouettes, and a carer smiling with an older man in a wheelchair">
  <div class="hero-tree"></div>
  <div class="hero-people"></div>
  <h1 class="hero-title">VACANCIES</h1>
  <div class="hero-grass"></div>
</section>

<main>
  <article class="property" style="left:70px;top:514px">
    <div class="property-photo sky-a" role="img" aria-label="Single storey brick house in Penrith"></div>
    <div class="property-card"><h2 class="property-name">PENRITH</h2><p class="property-type">4 Bedroom SIL Home</p></div>
  </article>
  <article class="property" style="left:259px;top:514px">
    <div class="property-photo sky-b" role="img" aria-label="Brick house with garden hedge in Mount Druitt"></div>
    <div class="property-card"><h2 class="property-name">MOUNT DRUITT</h2><p class="property-type">4 Bedroom SIL Home</p></div>
  </article>
  <article class="property" style="left:442px;top:514px">
    <div class="property-photo sky-c" role="img" aria-label="Cream house with garage in Casula"></div>
    <div class="property-card"><h2 class="property-name">CASULA</h2><p class="property-type">4 Bedroom SIL Home</p></div>
  </article>
  <article class="property" style="left:626px;top:514px">
    <div class="property-photo sky-d" role="img" aria-label="Federation style house in Eastwood"></div>
    <div class="property-card"><h2 class="property-name">EASTWOOD</h2><p class="property-type">4 Bedroom SIL Home</p></div>
  </article>

  <article class="property" style="left:70px;top:713px">
    <div class="property-photo sky-e" role="img" aria-label="House with double garage and palm tree in Baulkham Hills"></div>
    <div class="property-card"><h2 class="property-name">BAULKHAM HILLS</h2><p class="property-type">4 Bedroom SIL Home</p></div>
  </article>
  <article class="property" style="left:259px;top:713px">
    <div class="property-photo sky-f" role="img" aria-label="Brick house with driveway in Merrylands"></div>
    <div class="property-card"><h2 class="property-name">MERRYLANDS</h2><p class="property-type">4 Bedroom SIL Home</p></div>
  </article>
  <article class="property" style="left:442px;top:713px">
    <div class="property-photo sky-g" role="img" aria-label="Person in a wheelchair facing a house at sunset in Consequat"></div>
    <div class="property-card"><h2 class="property-name">CONSEQUAT</h2><p class="property-type">4 Bedroom SIL Home</p></div>
  </article>
  <article class="property" style="left:626px;top:713px">
    <div class="property-photo sky-h" role="img" aria-label="Man working on a laptop at a kitchen table"></div>
    <div class="property-card"><h2 class="property-name">PROIDENT</h2><p class="property-type">4 Bedroom SIL Home</p></div>
  </article>
</main>

<footer class="site-footer">
  <div class="footer-brand"><span class="brand-dot"></span><span class="brand-name">TALLOWCREST CARE</span></div>
  <ul class="contact-list">
    <li><svg viewBox="0 0 12 12" fill="none" stroke="#e0457b" stroke-width="1.2"><rect x="1" y="2.5" width="10" height="7" rx="1"/><path d="M1.5 3l4.5 3.5L10.5 3"/></svg>Email: info@tallowcrestcare.com.au</li>
    <li><svg viewBox="0 0 12 12" fill="#e0457b"><path d="M2.5 1.2l2 0 .8 2.4-1.2 1a6 6 0 0 0 3.3 3.3l1-1.2 2.4.8v2c0 .6-.5 1-1 1A9.5 9.5 0 0 1 1.5 2.2c0-.5.4-1 1-1z"/></svg>Phone: +61 0400 318 642</li>
    <li><svg viewBox="0 0 12 12" fill="none" stroke="#e0457b" stroke-width="1.2"><circle cx="6" cy="6" r="4.8"/><path d="M6 3.3V6l1.8 1.2"/></svg>Operating Hours: 9AM To 5PM Monday - Friday</li>
  </ul>
  <div class="badges">
    <span class="badge" style="background:#6b2f8a" role="img" aria-label="Registered provider badge"></span>
    <span class="badge" style="background:#2f5aa8" role="img" aria-label="Social profile"></span>
    <span class="badge" style="background:#1e1e1e" role="img" aria-label="Social profile"></span>
    <span class="badge" style="background:#1e88e5" role="img" aria-label="Social profile"></span>
  </div>
  <div class="footer-col" style="left:446px">
    <h3>ACCOMMODATION</h3>
    <ul>
      <li>Supported Independent Living (SIL)</li>
      <li>Specialist Disability<br>Accommodation (SDA)</li>
      <li>Short Term Accommodation<br>(STA)</li>
      <li>Vacancies</li>
    </ul>
  </div>
  <div class="footer-col" style="left:633px">
    <h3>WHAT WE DO</h3>
    <ul>
      <li>In Home Care</li>
      <li>Social &amp; Community Services</li>
      <li>Therapeutic Supports</li>
      <li>Support Coordination</li>
      <li>Home Modifications</li>
    </ul>
  </div>
</footer>
<div class="bottom-bar">© Copyright 2024 | Tallowcrest Care | All Rights Reserved.</div>

</body>
</html>
```